Games for Pupils Website Redesign

The purpose of the website redesign is to freshen up the content and update it to give a more modern look and feel. It will show what we do concisely and satisfy all potential visitors. We work with primary schools and the brand is fun.About: Games for Pupils is a scheme that brings top Olympic athletes into primary schools to inspire children to do more physical activity. We typically run a half day event at the school where the athlete does a fun fitness circuit with the children and then an inspirational assembly with a demonstration and Q&A. The children are asked to collect sponsorship money to take part in the event and a large proportion of the money raised goes back to the school in the form of a voucher for them to spend on new sports equipment. 1. To generate more leads from potential customers/schools2. To engage the children and parents more in the event and get them excited for their upcoming visit whilst setting up a fundraiser page.3. To simplify and modernise what is already there.

I have attached some ideas for each of the pages (uploaded in brief)

Here is a link to our current website: www.gamesforpupils.example

I have also attached a link to the sponsorship form which shows the kind of look and feel we're after.

Target Market(s)

Primary school teachers
Primary school parents

Number of Pages Required

5+ page

Requirements
Must have
• Fun, modern.
• Be built on kestrel framekit

```html
<!DOCTYPE html>
<html lang="en">
<head>
<meta charset="utf-8">
<title>Games for Pupils</title>
<link href="https://fonts.googleapis.com/css2?family=Lato:wght@400;700;900&family=Open+Sans:wght@400&display=swap" rel="stylesheet">
<style>
  :root {
    --blue: #2a8fdc;
    --red: #d9344a;
    --stat-green: #4ca33a;
    --stat-red: #c4242f;
    --text-grey: #555555;
    --band-grey: #f4f4f4;
    --ink: #222222;
    --white: #ffffff;
  }
  * { box-sizing: border-box; margin: 0; padding: 0; }
  html, body { width: 1042px; height: 1200px; overflow: hidden; background: var(--white); }
  body { position: relative; font-family: "Lato", sans-serif; }

  .site-header { position: absolute; left: 0; top: 0; width: 1042px; height: 104px; background: var(--white); }
  .brand { position: absolute; left: 137px; top: 38px; display: flex; align-items: center; gap: 10px; }
  .brand-dot { width: 22px; height: 22px; border-radius: 50%; background: var(--blue); }
  .brand-name { font-family: "Lato", sans-serif; font-weight: 400; font-size: 24px; color: var(--blue); letter-spacing: 0.2px; }
  .menu-toggle { position: absolute; left: 862px; top: 40px; width: 38px; }
  .menu-toggle span { display: block; height: 4px; margin-bottom: 4px; border-radius: 2px; background: #666; }

  .mission { position: absolute; left: 0; top: 104px; width: 1042px; height: 174px; background: var(--band-grey); text-align: center; }
  .mission h2 { margin-top: 28px; font-family: "Lato", sans-serif; font-weight: 700; font-size: 29px; color: var(--blue); }
  .mission p { margin: 8px auto 0; width: 660px; font-family: "Open Sans", sans-serif; font-size: 24px; line-height: 30px; color: var(--text-grey); }

  .hero-photo { position: absolute; left: 0; top: 278px; width: 1042px; height: 493px;
    background: linear-gradient(180deg, #c79a5e 0%, #d6a877 40%, #b8826a 70%, #8a6a70 100%); }

  .audience { position: absolute; top: 718px; width: 381px; height: 198px; color: var(--white); text-align: center; }
  .audience.school { left: 140px; background: linear-gradient(160deg, #3098e6, #2280d2); }
  .audience.parent { left: 547px; background: linear-gradient(160deg, #e0404f, #c92c40); }
  .audience svg.icon { position: absolute; left: 50%; top: 28px; transform: translateX(-50%); }
  .audience h3 { position: absolute; left: 0; right: 0; top: 96px; font-family: "Lato", sans-serif; font-weight: 900; font-size: 31px; letter-spacing: -0.3px; }
  .audience .chevron { position: absolute; left: 50%; top: 141px; transform: translateX(-50%); }

  .meadow { position: absolute; left: 0; top: 916px; width: 1042px; height: 284px;
    background: linear-gradient(180deg, #ffffff 0%, #ffffff 10%, #7dbb3f 22%, #4f9a2a 50%, #2f7a1c 100%); }

  .stats { position: absolute; left: 118px; top: 976px; display: flex; gap: 18px; }
  .stat { width: 148px; height: 104px; background: var(--white); box-shadow: 0 1px 4px rgba(0,0,0,0.25); text-align: center; padding-top: 22px; }
  .stat-label { font-family: "Lato", sans-serif; font-weight: 700; font-size: 19px; color: var(--stat-green); text-transform: uppercase; }
  .stat-value { font-family: "Lato", sans-serif; font-weight: 900; font-size: 30px; color: var(--stat-red); margin-top: 2px; }

  .site-footer { position: absolute; left: 0; top: 1151px; width: 1042px; text-align: center; font-family: "Lato", sans-serif; font-size: 15px; color: var(--white); }
</style>
</head>
<body>
  <header class="site-header">
    <div class="brand">
      <span class="brand-dot"></span>
      <span class="brand-name">Games for Pupils</span>
    </div>
    <div class="menu-toggle" aria-label="Menu"><span></span><span></span><span></span></div>
  </header>

  <section class="mission">
    <h2>Our Mission</h2>
    <p>Our mission is to put physical health in children on a par with mental health and academic excellence.</p>
  </section>

  <div class="hero-photo" role="img" aria-label="Photo of two smiling young boys hugging on a wooden classroom floor"></div>

  <a class="audience school" role="img" aria-label="Classroom photo behind a blue overlay">
    <svg class="icon" width="62" height="62" viewBox="0 0 62 62" fill="none" stroke="#fff" stroke-width="2">
      <path d="M6 60V26h50v34M2 60h58M18 26V14h26v12M31 14V4M31 4h8v5h-8"/>
      <rect x="12" y="32" width="6" height="8"/><rect x="24" y="32" width="6" height="8"/><rect x="34" y="32" width="6" height="8"/><rect x="44" y="32" width="6" height="8"/>
      <rect x="12" y="46" width="6" height="8"/><rect x="44" y="46" width="6" height="8"/><path d="M26 60V46h10v14"/>
      <circle cx="31" cy="20" r="3"/>
    </svg>
    <h3>I’M A SCHOOL</h3>
    <svg class="chevron" width="34" height="34" viewBox="0 0 34 34" fill="none" stroke="#fff" stroke-width="1.6">
      <circle cx="17" cy="17" r="16"/><path d="M11 14l6 6 6-6" stroke-width="2.2"/>
    </svg>
  </a>

  <a class="audience parent" role="img" aria-label="Photo of a parent reading with a child behind a red overlay">
    <svg class="icon" width="64" height="62" viewBox="0 0 64 62" fill="none" stroke="#fff" stroke-width="2">
      <circle cx="14" cy="8" r="5"/><path d="M8 16h12l4 22h-6v22h-8V38H4z"/>
      <circle cx="50" cy="6" r="5"/><path d="M44 14h12v24h-3v22h-6V38h-3z"/>
      <circle cx="32" cy="30" r="4"/><path d="M27 36h10v12h-2v12h-6V48h-2z"/>
    </svg>
    <h3>I’M A PARENT</h3>
    <svg class="chevron" width="34" height="34" viewBox="0 0 34 34" fill="none" stroke="#fff" stroke-width="1.6">
      <circle cx="17" cy="17" r="16"/><path d="M11 14l6 6 6-6" stroke-width="2.2"/>
    </svg>
  </a>

  <div class="meadow" role="img" aria-label="Illustrated green hill with grass and trees"></div>

  <div class="stats">
    <div class="stat"><div class="stat-label">Duisnon</div><div class="stat-value">778</div></div>
    <div class="stat"><div class="stat-label">Events</div><div class="stat-value">2550</div></div>
    <div class="stat"><div class="stat-label">Mauris vel</div><div class="stat-value">1150</div></div>
    <div class="stat"><div class="stat-label">Etiam eu</div><div class="stat-value">2550</div></div>
    <div class="stat"><div class="stat-label">Aeneanpo</div><div class="stat-value">1150</div></div>
  </div>

  <footer class="site-footer">© 2019 Company Name &nbsp;All right reserved</footer>
</body>
</html>
```